"The Plumewright" nails, eyelash extensions and hair extensions. Need an eye catching design for bu

Need an eye catching design focusing on eyelash extensions, nail extensions and hair extensions. I like the colour green, black, glitter, pink?! need the design to be innovative and 'POP'. I'd like more emphasis on lashes and nails.
I'd like the business name and my phone number on the front of card.
Would really like something different and unique.
"The Plumewright"
Nails, Eyelash & Hair Extensions
Mira
0471526093

Target Market(s)

20-40

Industry/Entity Type

Beauty Salon

Contact Information for Business Card

Id like my business name, My name and phone number on the front of card
"The Plumewright".
Mira.
0471526093.
Id like some catchy design involving long lashes with possibly glitter, long hair and nails. Id like the lashes to be the first thing you see at first glance. I'm open to your creative flair. Just need the business card design to 'POP'! I like the colours green, black, pink, silver or gold glitter. wether it's pop art, 3d drawn pictures, isolated pics of lash, nails or hair, card design could be in black and white with isolated colours added..i'm open to your creative flair. use a font which stands out and easy to read.
(The back of the card will be used for writing appointment times.)

Font styles to use
Serif

Colors
6b449b
e667a6
25b39d

Requirements
Must have
• Long lashes, hair, nails.
• one sided
Nice to have
• bright catchy colours, innovative, uniqueness

```html
<!DOCTYPE html>
<html lang="en">
<head>
<meta charset="utf-8">
<title>The Plumewright – Business Card</title>
<link href="https://fonts.googleapis.com/css2?family=Open+Sans:wght@600&display=swap" rel="stylesheet">
<style>
  :root {
    --stage: #f4f3f6;
    --purple: #6b449b;
    --teal: #25b39d;
    --silver: #d9d9dd;
    --photo-light: #f2f2f2;
    --photo-mid: #cfcfcf;
    --photo-dark: #8e8e8e;
    --photo-shadow: #5e5e5e;
    --white: #ffffff;
  }
  html, body {
    margin: 0;
    width: 1200px;
    height: 900px;
    overflow: hidden;
    background: var(--stage);
    font-family: "Open Sans", Arial, sans-serif;
  }
  .business-card {
    position: absolute;
    left: 111px;
    top: 147px;
    width: 978px;
    height: 605px;
    overflow: hidden;
    box-shadow: 0 10px 30px rgba(0, 0, 0, 0.18);
  }
  .portrait-area {
    position: absolute;
    inset: 0;
    background:
      radial-gradient(ellipse 32% 40% at 88% 28%, var(--photo-shadow) 0%, transparent 75%),
      radial-gradient(ellipse 30% 45% at 55% 55%, var(--photo-dark) 0%, transparent 70%),
      radial-gradient(ellipse 45% 55% at 75% 45%, var(--photo-mid) 0%, transparent 80%),
      linear-gradient(100deg, var(--photo-light) 0%, var(--photo-light) 28%, var(--photo-mid) 100%);
  }
  .wave-band {
    position: absolute;
    inset: 0;
    width: 100%;
    height: 100%;
  }
  .brand-dot {
    position: absolute;
    left: 207px;
    top: 97px;
    width: 136px;
    height: 136px;
    border-radius: 50%;
    background: var(--teal);
  }
  .brand-name {
    position: absolute;
    left: 31px;
    top: 282px;
    margin: 0;
    font-size: 68px;
    font-weight: 600;
    line-height: 1;
    color: var(--purple);
    white-space: nowrap;
  }
  .contact {
    position: absolute;
    right: 63px;
    top: 427px;
    text-align: right;
    color: var(--white);
  }
  .contact-name {
    margin: 0;
    font-size: 46px;
    font-weight: 600;
    line-height: 1;
  }
  .contact-phone {
    display: flex;
    align-items: center;
    justify-content: flex-end;
    gap: 12px;
    margin: 15px 0 0;
    height: 36px;
    font-size: 36px;
    font-weight: 600;
    line-height: 1;
  }
  .phone-icon {
    width: 32px;
    height: 32px;
    flex: none;
  }
</style>
</head>
<body>
  <div class="business-card">
    <div class="portrait-area" role="img" aria-label="Black and white beauty photograph: a woman with long eyelash extensions, long flowing hair extensions and long manicured nails"></div>

    <svg class="wave-band" viewBox="0 0 652 403" preserveAspectRatio="none" aria-hidden="true">
      <path d="M0,267 C80,317 150,338 225,332 C330,322 430,196 535,191 C590,189 630,210 652,234"
            fill="none" stroke="var(--teal)" stroke-width="5"/>
      <path d="M0,275 C80,325 150,346 225,340 C330,330 430,204 535,199 C590,197 630,218 652,242"
            fill="none" stroke="var(--silver)" stroke-width="4"/>
      <path d="M0,278 C80,328 150,349 225,343 C330,333 430,207 535,202 C590,200 630,221 652,245 L652,403 L0,403 Z"
            fill="var(--purple)"/>
    </svg>

    <div class="brand-dot" aria-hidden="true"></div>
    <h1 class="brand-name">The Plumewright</h1>

    <div class="contact">
      <p class="contact-name">Mira</p>
      <p class="contact-phone">
        <span>0471526093</span>
        <svg class="phone-icon" viewBox="0 0 24 24" aria-hidden="true">
          <path fill="var(--white)" d="M6.6 10.8c1.4 2.8 3.8 5.1 6.6 6.6l2.2-2.2c.3-.3.7-.4 1-.2 1.1.4 2.3.6 3.6.6.6 0 1 .4 1 1V20c0 .6-.4 1-1 1C10.6 21 3 13.4 3 4c0-.6.4-1 1-1h3.5c.6 0 1 .4 1 1 0 1.3.2 2.5.6 3.6.1.3 0 .7-.2 1l-2.3 2.2z"/>
        </svg>
      </p>
    </div>
  </div>
</body>
</html>
```